Lanternfield Drinks business cards

We need a business card design for our new logo. The company is modern, progressive, professional, yet approachable. The key products are ready to drink bottles and cans of coffee based beverages.
These cards will be a critical part of the first impression made by our sales organization, business development team, and all external facing personnel.
Card can be a vertical or horizontal orientation.

Target Market(s)

Customers, suppliers, business partners

Industry/Entity Type

Business

Contact Information for Business Card

Business cards should feature Company Name and Logo.

Font styles to use
Serif

Colors

Designer to choose colors to be used in the design.

Requirements
Must have
• Strong readability of Name, phone #, mobile number and email address.
• Job title, website url, Street Address, and other details can be secondary level readability.
Nice to have
• High impact, simplistic quality design.
• Ok to utilize the 'H in the box' separate from the company name

```html
<!DOCTYPE html>
<html lang="en">
<head>
<meta charset="utf-8">
<title>Lanternfield Drinks business cards</title>
<link href="https://fonts.googleapis.com/css2?family=Cinzel:wght@600&family=Lora:wght@400;500&display=swap" rel="stylesheet">
<style>
  :root {
    --bg: #121212;
    --paper: #ffffff;
    --paper-shade: #eeeeee;
    --orange: #ea6a3c;
    --orange-light: #f09a62;
    --gold: #f2a623;
    --ink-light: #fff6ee;
    --accent: #e8642f;
  }
  * { margin: 0; padding: 0; box-sizing: border-box; }
  html, body { width: 1200px; height: 864px; overflow: hidden; background: var(--bg); }
  .stage {
    width: 1200px; height: 864px;
    display: flex; align-items: center; justify-content: center; gap: 60px;
  }
  .card {
    position: relative; width: 525px; height: 300px;
    background: var(--paper); overflow: hidden;
    box-shadow: 0 14px 30px rgba(0,0,0,.6);
    font-family: "Lora", Georgia, serif;
  }
  .band {
    position: absolute; left: 0; right: 0; bottom: 0;
    background: linear-gradient(160deg, var(--orange) 0%, var(--orange-light) 55%, var(--orange) 100%);
  }
  .stripe { position: absolute; left: 0; right: 0; height: 5px; background: var(--gold); }

  /* front */
  .card--front .band { top: 138px; }
  .card--front .stripe { top: 128px; }
  .brand-mark {
    position: absolute; top: 40px; right: 36px;
    display: flex; align-items: center; gap: 10px;
  }
  .brand-mark__square { width: 30px; height: 30px; border: 4px solid var(--accent); }
  .brand-mark__name {
    font-family: "Cinzel", "Times New Roman", serif; font-weight: 600;
    font-size: 20px; color: var(--accent); letter-spacing: .5px;
  }
  .name-tab {
    position: absolute; top: 148px; right: 70px; width: 190px; height: 46px;
    background: var(--paper-shade);
    clip-path: polygon(0 0, 100% 0, 92% 100%, 8% 100%);
    text-align: center; padding-top: 6px;
  }
  .name-tab__name {
    font-family: "Cinzel", "Times New Roman", serif; font-weight: 600;
    font-size: 13px; color: var(--accent); letter-spacing: .5px;
  }
  .name-tab__title { font-size: 11px; color: var(--accent); }
  .contact-list {
    position: absolute; left: 26px; top: 170px; list-style: none;
    font-size: 11.5px; color: var(--ink-light); line-height: 20px;
  }
  .contact-list li { display: flex; align-items: center; gap: 10px; }
  .contact-list svg { width: 11px; height: 11px; }
  .address {
    position: absolute; left: 330px; top: 232px;
    font-size: 11.5px; color: var(--ink-light); line-height: 17px; font-style: normal;
  }

  /* back */
  .card--back .band { top: 100px; }
  .card--back .stripe { top: 86px; }
  .card--back .stripe--second { top: 274px; }
  .bottle-outlines {
    position: absolute; top: 10px; right: 40px; width: 160px; height: 70px;
    background: linear-gradient(180deg, rgba(0,0,0,0) 0%, rgba(0,0,0,.03) 100%);
  }
  .back-brand {
    position: absolute; left: 40px; top: 150px;
    display: flex; align-items: center; gap: 14px;
  }
  .back-brand__square { width: 46px; height: 46px; border: 5px solid var(--paper); }
  .back-brand__name {
    font-family: "Cinzel", "Times New Roman", serif; font-weight: 600;
    font-size: 34px; color: var(--paper); letter-spacing: 1px;
  }
</style>
</head>
<body>
<main class="stage">

  <section class="card card--front" aria-label="Card front">
    <div class="brand-mark">
      <span class="brand-mark__square"></span>
      <span class="brand-mark__name">Lanternfield Drinks</span>
    </div>
    <div class="stripe"></div>
    <div class="band"></div>
    <div class="name-tab">
      <div class="name-tab__name">DANIEL OKAFOR</div>
      <div class="name-tab__title">Managing Director</div>
    </div>
    <ul class="contact-list">
      <li><svg viewBox="0 0 12 12"><path d="M3 1l2 2-1 1.5a7 7 0 0 0 3.5 3.5L9 7l2 2-1.5 2A9 9 0 0 1 1 2.5z" fill="var(--gold)"/></svg>555.014.2231</li>
      <li><svg viewBox="0 0 12 12"><rect x="3" y="1" width="6" height="10" rx="1" fill="none" stroke="var(--gold)" stroke-width="1.4"/></svg>555.019.7740</li>
      <li><svg viewBox="0 0 12 12"><rect x="1" y="3" width="10" height="7" fill="none" stroke="var(--gold)" stroke-width="1.4"/><path d="M1 3l5 4 5-4" fill="none" stroke="var(--gold)" stroke-width="1.2"/></svg>dan@lanternfielddrinks.com</li>
      <li><svg viewBox="0 0 12 12"><circle cx="6" cy="6" r="4.5" fill="none" stroke="var(--gold)" stroke-width="1.4"/><path d="M1.5 6h9M6 1.5v9" stroke="var(--gold)" stroke-width="1"/></svg>www.lanternfielddrinks.com</li>
    </ul>
    <address class="address">48 Meadow Row<br>Harlow Point, NY 10990</address>
  </section>

  <section class="card card--back" aria-label="Card back">
    <div class="bottle-outlines" role="img" aria-label="Faint outlines of coffee bottles and cans"></div>
    <div class="stripe"></div>
    <div class="band"></div>
    <div class="stripe stripe--second"></div>
    <div class="back-brand">
      <span class="back-brand__square"></span>
      <span class="back-brand__name">LANTERNFIELD DRINKS</span>
    </div>
  </section>

</main>
</body>
</html>
```